Weightloss company needs Business Card

We want a business card that is clean and professional, yet portrays that we are a friendly, innovative, and versatile program designed to fit the needs of our clients.
I would like there to be 2 sides, one side having an appointment card, and the other side containing the logo and business information. There can be decorations on both sides. The logo is attached.

Target Market(s)

Men and women 40-60

Industry/Entity Type

Business

Contact Information for Business Card

Font styles to use
Sans Serif

Requirements
Must have
• The logo, space for business information
Nice to have
• The colors in the logo
Should not have
• No pictures of people or food

```html
<!DOCTYPE html>
<html lang="en">
<head>
<meta charset="utf-8">
<title>Renew Turn Wellness – Business Card</title>
<link rel="stylesheet" href="https://fonts.googleapis.com/css2?family=Open+Sans:wght@400;600;700;800&display=swap">
<style>
  :root {
    --page-bg: #eceae6;
    --brand-red: #e8194a;
    --brand-rose: #fbd5df;
    --brand-rose-soft: #fff1f4;
    --cyan-light: #5fe4fb;
    --cyan-deep: #1ab5da;
    --ink: #3c3c3c;
    --muted: #555;
    --rule: #4a4a4a;
    --white: #ffffff;
    --card-grey: #dcdcdc;
  }
  * { margin: 0; padding: 0; box-sizing: border-box; }
  html, body {
    width: 1200px; height: 843px; overflow: hidden;
    background: var(--page-bg);
    font-family: "Open Sans", Arial, sans-serif;
  }
  .canvas { position: relative; width: 1200px; height: 843px; }

  .card {
    position: absolute; width: 620px; height: 354px;
    border-radius: 26px; overflow: hidden;
    box-shadow: 0 10px 26px rgba(0,0,0,.22);
  }
  .brand-name { color: var(--brand-red); font-weight: 800; line-height: 1; }

  /* Appointment side */
  .appointment-card {
    left: 60px; top: 60px;
    background: linear-gradient(180deg, var(--white) 0%, #f6f6f6 55%, var(--card-grey) 100%);
  }
  .appointment-card .brand-name { position: absolute; right: 34px; top: 28px; text-align: right; }
  .appointment-card .brand-name span { display: block; font-size: 21px; }
  .appointment-card .brand-name span + span { font-size: 15px; margin-top: 2px; }
  .appointment-title {
    position: absolute; left: 40px; top: 70px;
    color: var(--brand-red); font-weight: 700; font-size: 22px;
  }
  .appointment-rows {
    position: absolute; left: 40px; right: 34px; top: 128px;
    display: flex; flex-direction: column; gap: 30px;
  }
  .appointment-row { display: flex; align-items: flex-end; gap: 10px; font-size: 15px; color: var(--ink); }
  .appointment-row .blank { border-bottom: 1.5px solid var(--rule); height: 1px; }
  .appointment-row .blank-date { width: 230px; }
  .appointment-row .blank-time { width: 150px; }
  .appointment-row .label-time { margin-left: 16px; }
  .appointment-note {
    position: absolute; left: 40px; bottom: 30px;
    font-size: 12.5px; color: var(--muted); font-weight: 600;
  }

  /* Contact side */
  .contact-card { left: 520px; top: 440px; background: var(--white); }
  .contact-card .card-art { position: absolute; inset: 0; }
  .brand-mark-area {
    position: absolute; left: 45px; top: 17px; width: 320px; height: 320px;
    border-radius: 50%;
    background: radial-gradient(circle, var(--brand-rose-soft) 0%, var(--brand-rose) 100%);
  }
  .contact-card .brand-name {
    position: absolute; left: 60px; top: 124px; width: 290px; text-align: center;
  }
  .contact-card .brand-name span { display: block; font-size: 36px; letter-spacing: -0.5px; }
  .contact-card .brand-name span + span { font-size: 26px; margin-top: 4px; }
  .contact-details { position: absolute; right: 34px; top: 96px; text-align: right; color: var(--white); }
  .person-name { font-size: 19px; font-weight: 600; letter-spacing: .5px; }
  .person-role { font-size: 14px; letter-spacing: .5px; margin-bottom: 16px; }
  .address { font-size: 14px; line-height: 1.3; margin-bottom: 6px; }
  .contact-line {
    display: flex; justify-content: flex-end; align-items: center; gap: 10px;
    font-size: 14px; line-height: 1.45;
  }
  .contact-line svg { width: 14px; height: 14px; flex: none; }
</style>
</head>
<body>
<main class="canvas">

  <section class="card appointment-card" aria-label="Appointment card">
    <div class="brand-name"><span>Renew Turn</span><span>Wellness</span></div>
    <h2 class="appointment-title">Next Appointment</h2>
    <div class="appointment-rows">
      <div class="appointment-row"><span>Date</span><span class="blank blank-date"></span><span class="label-time">Time</span><span class="blank blank-time"></span><span>am/pm</span></div>
      <div class="appointment-row"><span>Date</span><span class="blank blank-date"></span><span class="label-time">Time</span><span class="blank blank-time"></span><span>am/pm</span></div>
      <div class="appointment-row"><span>Date</span><span class="blank blank-date"></span><span class="label-time">Time</span><span class="blank blank-time"></span><span>am/pm</span></div>
    </div>
    <p class="appointment-note">Please give 24 hours notice of cancellation or a fee may be charged</p>
  </section>

  <section class="card contact-card" aria-label="Business information card">
    <svg class="card-art" viewBox="0 0 620 354" preserveAspectRatio="none" aria-hidden="true">
      <defs>
        <linearGradient id="cyanBand" x1="0" y1="0" x2="0" y2="1">
          <stop offset="0" stop-color="#5fe4fb"/>
          <stop offset="1" stop-color="#1ab5da"/>
        </linearGradient>
      </defs>
      <rect x="0" y="0" width="620" height="354" fill="url(#cyanBand)"/>
      <path d="M0 0 H230 A168 168 0 0 1 230 354 H0 Z" fill="#ffffff"/>
      <circle cx="205" cy="177" r="175" fill="#ffffff"/>
    </svg>
    <div class="brand-mark-area" role="img" aria-label="Large circular brand symbol decoration"></div>
    <div class="brand-name"><span>Renew Turn</span><span>Wellness</span></div>
    <div class="contact-details">
      <p class="person-name">MARIA HOLDEN</p>
      <p class="person-role">CEO/FOUNDER</p>
      <p class="address">214 Birchwood Court<br>Fairbanks, Alaska 99701</p>
      <p class="contact-line">907 555 0142
        <svg viewBox="0 0 16 16"><path d="M4 1l3 3-2 2c1 2 3 4 5 5l2-2 3 3-2 3C7 15 1 9 1 3z" fill="#fff"/></svg></p>
      <p class="contact-line">907 555 0187
        <svg viewBox="0 0 16 16"><rect x="4" y="2" width="8" height="12" rx="1.5" fill="none" stroke="#fff" stroke-width="1.6"/><circle cx="8" cy="12" r="1" fill="#fff"/></svg></p>
      <p class="contact-line">907 555 0163
        <svg viewBox="0 0 16 16"><rect x="4" y="1" width="8" height="5" fill="#fff"/><rect x="1" y="6" width="14" height="6" rx="1" fill="#fff"/><rect x="4" y="10" width="8" height="5" fill="#fff" stroke="#1fb8dc"/></svg></p>
      <p class="contact-line">hello@renewturn.com
        <svg viewBox="0 0 16 16"><rect x="1" y="3" width="14" height="10" rx="1" fill="#fff"/><path d="M1 3l7 6 7-6" fill="none" stroke="#1fb8dc" stroke-width="1.4"/></svg></p>
      <p class="contact-line">www.renewturn.com
        <svg viewBox="0 0 16 16"><circle cx="8" cy="8" r="7" fill="#fff"/><path d="M1 8h14M8 1c-3 4-3 10 0 14M8 1c3 4 3 10 0 14" fill="none" stroke="#1fb8dc" stroke-width="1.1"/></svg></p>
    </div>
  </section>

</main>
</body>
</html>
```